Velmora Gems - High end custom Jewelry website

I need a web design for an online custom jewelry company called Velmora Gems. (www.velmoragems-demo.com) this company specializes in high-end custom made engagement rings, wedding bands and jewelry of all kinds (necklaces, earrings, bracelets etc)All our jewelry uses diamonds so there must be a focus on diamonds on every type of jewelry we will be designing off the website.

We are a company located in New York City but our website will
aim to cater to international, national clients and as well as New York city residents.The company low overhead provides diamonds and precious metal at a discounted costs compared to its competitors. Velmora Gems makes unique custom diamond jewelry of a higher quality and at a lower price than carriage trade retail jewellers. (meaning that our company allows our customers to save money on diamond jewelry then they would if they bought from any known store or company)

The website will act as a tool for our customers to create their own jewelry. The way they will do this is by uploading pictures of what they like, they can post any pictures they want (from drawings, to actual copy and pasted pictures from other websites of designs) From these designs we will create a 3D digital image of the jewelry they like and customize it - however they want (colours, size etc) and then give them a quote in price. From the quote they will either approve it and we can have it made for them in 1 weeks time. If they decline it we will try to do whatever it is they want for the design to suit their needs.

We want the website to be simple and user friendly since people will be working on it to create their own individual jewelry pieces. Therefore some useful headings should include:

"Custom Jewellery" or something like "your design" "Custom Design"

a drop heading here should show the following steps into creating the jewelry.

step 1:
upload pictures of the designs you like
step 2:
What is your ring size?
Step 3:
What setting would you like your ring in? platinum, 14k etc..
Step 4:
What is your budget?
Step 5 :
Once you’ve uploaded pictures and give an explanation of what you want then we will contact you by phone or email and proceed to design your ring. Give us your contact info in this step.

Other then that other headings id like to see on the site are:

"Home"
main page with appealing picture which I can later add text to it explaining our company

"About us"
will include a brief section of who we are

"Wedding/engagment"

We are based in New York City and our company offers a one-to-one personal service to our clients ensuring their expectations are well met and, if we can help it, surpassed. We are a personal shopping and diamond supplier to individuals. Custom design is our speciality weather it be wedding ring, engagement ring or anniversary ring we aim to create distinctive designs that both reflect your personality as well as the beauty of the gemstones used in your piece. We use platinum, 14l-18k gold and diamonds to whatever it is that you may desire.
We in our company believe that we are privileged to be a part of one of the biggest events in our customer’s lives, and we pride ourselves on making sure that our customers have the best experience possible. As the diamond is the center piece of every engagement ring, we at VG make sure that our clients find the best diamond possible that is within their budget. Similarly, we work with established jewellery artisans from Belgium to provide the highest possible craftsmanship to a ring design of your choice. We make sure that our rings are made by the true and tried traditional methods focused on quality rather than quantity and of course our diamonds are QRB certified.

Diamonds

A section that explains where our diamonds come from. A heading will drop down here that is a diamond guide, as shown below.
Diamond Guide

An overview of the 4 C’s and different settings, a section for a brief education on diamonds.
Client Experiences

A section where clients share their experiences with Velmora Gems and can post pictures and share stories about their engagement etc.

The colour i would like to see are white and black, white and dark blue or royal blue. I don't think pastel colours will look good with this, maybe accents of purple or something pastel but for the main colours I want to keep it classic and sophisticated since it is a diamond company.

"Sign in | Check out"
where users are able to create a profile and upload their pictures and create their designs..

and a "search section"

or something along these lines or if you can incorporate both:

Exquisite craftsmanship Finest quality diamonds
Will beat any competitors price by twenty to seventy percent guaranteed
Price quotes whitin24 hours

Upload design picture or sketch
Receive price quote within 24hours
Receive and approve free customized design
Receive you jewelry in 1 week or less

Engagment Ring or necklace, earring, etc
Name
EMail
phone
Competitior Link
Budget

The final design should communicate that Velmora Gems is a custom jewelry site that allows individuals to personalize any type of jewellery they want with diamonds - at a fraction of the cost in comparison to any other out there. Our team works very hard to ensure that you will be so involved in the custom order process that there is no chance of something not being made to your requests. Jewelry is made to the highest standard or it does not ship in the first place. In the event a custom order does not suit a customer, we will take returns within 14 days of delivery less a 25% restocking fee.

Target Market(s)

middle class and upper class people ages 25-45

Industry/Entity Type

Digital

Requirements
Must have
• We have the logo now that I will attach BUT if you want to design something else please feel free ! I am open to all designs and ideas.
My logo now is simply a sketch so even if we make it look a bit more professional and classy I would like that, I think I want to keep it simple just black and white and maybe make the diamond shiny if possible. other then black in white I liked the gold and black combination too.. but as I said open to any other creative ideas!

can take pictures of jewelry off this website:
http://www.plinthwaredesigns.example/library/rings.html
Nice to have
• We already have a logo but we would like to see a banner or something that indicated saving money on diamond jewelry without it looking tacky or too cheap..

Also would like to see artistic pictures if you can of jewelry alongside very simple designs of jewelry that the masses like, (anything trendy or appealing to the eye)

cursive or elegant writing could be nice, flash could also be incorporated in the main page..

Should not have
• Nothing to old fashioned, when I mean elegant maybe just the the name of the company in cursive writing (Velmora Gems) but the actual headings and font on the website to be in a widely used font on jewelry websites. Please no hot pink colours or anything neon..
no times new roman font..

```html
<!DOCTYPE html>
<html lang="en">
<head>
<meta charset="utf-8">
<title>Velmora Gems</title>
<link href="https://fonts.googleapis.com/css2?family=Source+Sans+3:wght@300;400;600&display=swap" rel="stylesheet">
<style>
:root{
  --ink:#1a1a1a;
  --nav:#1c1c1c;
  --hero:#000;
  --accent:#3f5fb8;
  --navy:#07073a;
  --navy-2:#14145a;
  --lilac:#8d8dd8;
  --submit:#5b5b9e;
  --rule:#d6d6d6;
  --footer:#f2f2f2;
  --muted:#444;
}
*{box-sizing:border-box;margin:0;padding:0}
html,body{width:1094px;height:1200px;overflow:hidden;background:#fff}
body{position:relative;font-family:"Source Sans 3",Arial,sans-serif;color:var(--ink);font-weight:300}
.abs{position:absolute}

/* header */
.brand{left:143px;top:38px;display:flex;align-items:center;gap:10px;font-size:24px;font-weight:400;color:var(--ink)}
.brand-dot{width:14px;height:14px;border-radius:50%;background:var(--ink)}
.phone{left:489px;top:20px;display:flex;align-items:center;gap:7px;font-size:16px;font-weight:400}
.phone-icon{width:24px;height:24px;border-radius:50%;background:#111;display:flex;align-items:center;justify-content:center}
.util{left:630px;top:26px;display:flex;font-size:11px;font-weight:400}
.util a{color:var(--ink);text-decoration:none;padding:0 8px;border-left:1px solid #bbb;line-height:20px}
.util a:first-child{border-left:none}
.search{left:832px;top:20px;width:121px;height:26px;border:1px solid #ccc;font-size:11px;font-weight:400;padding:5px 8px;display:flex;justify-content:space-between;align-items:center}
.nav{left:438px;top:70px;height:38px;display:flex;background:var(--nav)}
.nav a{color:#fff;text-decoration:none;font-size:11.5px;font-weight:400;display:flex;align-items:center;justify-content:center;border-left:1px solid #555}
.nav a:first-child{border-left:none}

/* hero */
.hero{left:0;top:127px;width:1094px;height:396px;background:radial-gradient(ellipse at 60% 30%,#262626 0%,#0a0a0a 55%,#000 100%)}
.hero-title{left:143px;top:70px;font-size:42px;line-height:44px;color:#ddd}
.hero-sub{left:143px;top:168px;font-size:20px;line-height:25px;color:#ccc}
.hero-btn{left:143px;top:239px;width:79px;height:35px;background:var(--accent);color:#fff;font-size:14px;font-weight:400;display:flex;align-items:center;justify-content:center}
.dots{left:145px;top:316px;display:flex;gap:4px}
.dots span{width:15px;height:15px;border-radius:50%;background:#444}
.dots .on{background:var(--accent)}
.hero-photo{left:475px;top:24px;width:480px;height:341px;border-radius:40% 45% 45% 40%;background:radial-gradient(ellipse at 50% 50%,#9a9a9a 0%,#4a4a4a 45%,rgba(0,0,0,0) 72%)}
.arrow{top:167px;width:64px;height:64px;background:#3a3a3a;display:flex;align-items:center;justify-content:center}

/* categories */
.cat{top:547px;width:278px;height:261px;text-align:center}
.cat-photo{width:140px;height:130px;margin:4px auto 0;border-radius:50%;background:radial-gradient(circle,#d8d8d8 0%,#eeeeee 50%,#fff 72%)}
.cat h3{font-size:20px;font-weight:300;margin-top:30px}
.cat p{font-size:12px;line-height:17px;margin-top:5px}
.more{display:inline-flex;align-items:center;gap:4px;background:#1c1c1c;color:#ccc;font-size:12.5px;padding:0 7px;height:27px;margin-top:14px}
.vrule{top:547px;width:1px;height:261px;background:var(--rule)}

/* panels */
.panel{top:852px;width:389px;height:175px;background:linear-gradient(135deg,var(--navy) 0%,var(--navy-2) 100%);color:#fff}
.panel h2{position:absolute;font-size:20px;font-weight:300}
.custom-sub{left:115px;top:46px;font-size:12.5px;color:var(--lilac);font-weight:400}
.custom-body{left:115px;top:68px;width:252px;font-size:12px;line-height:19.5px;color:#ddd;text-align:justify}
.more-light{left:119px;top:128px;background:#fff;color:#333;font-size:12.5px;height:26px;padding:0 7px;display:flex;align-items:center;gap:4px}
.field{height:24px;background:#fff;color:#222;font-size:11px;font-weight:400;padding:0 9px;display:flex;align-items:center;border-radius:2px;width:168px}
.submit{width:56px;height:24px;background:var(--submit);color:#fff;font-size:12px;font-weight:600;display:flex;align-items:center;justify-content:center;border-radius:2px}

/* footer */
.footer{left:0;top:1060px;width:1094px;height:140px;background:var(--footer);border-top:1px solid #e2e2e2}
.footer-lines{left:144px;top:22px;font-size:10.5px;line-height:19.5px;color:var(--muted)}
.connect{right:144px;top:22px;font-size:10.5px;color:var(--muted);text-align:right}
.social{display:flex;gap:6px;margin-top:9px;justify-content:flex-end}
.social span{width:21px;height:21px;border-radius:50%;background:#3b5f99}
.footer-rule{left:143px;top:95px;width:810px;height:1px;background:#d0d0d0}
.copy{left:0;top:108px;width:1094px;text-align:center;font-size:10.5px;color:var(--muted)}
</style>
</head>
<body>

<header>
  <div class="abs brand"><span class="brand-dot"></span>Velmora Gems</div>
  <div class="abs phone">
    <span class="phone-icon">
      <svg width="13" height="13" viewBox="0 0 24 24"><path fill="#fff" d="M6.6 10.8a15 15 0 0 0 6.6 6.6l2.2-2.2c.3-.3.7-.4 1-.2 1.1.4 2.3.6 3.6.6.6 0 1 .4 1 1V20c0 .6-.4 1-1 1A17 17 0 0 1 3 4c0-.6.4-1 1-1h3.5c.6 0 1 .4 1 1 0 1.3.2 2.5.6 3.6.1.3 0 .7-.2 1z"/></svg>
    </span>414.XXX.XXXX
  </div>
  <nav class="abs util"><a href="#">Login</a><a href="#">My Account</a><a href="#">Shopping Cart</a></nav>
  <div class="abs search">Search
    <svg width="14" height="14" viewBox="0 0 20 20"><circle cx="8" cy="8" r="5.5" fill="#dfe9f5" stroke="#6b8fbf" stroke-width="1.8"/><line x1="12" y1="12" x2="18" y2="18" stroke="#c9a44a" stroke-width="3" stroke-linecap="round"/></svg>
  </div>
  <nav class="abs nav">
    <a href="#" style="width:96px">HOME</a>
    <a href="#" style="width:96px">ABOUT US</a>
    <a href="#" style="width:99px">SERVICES</a>
    <a href="#" style="width:105px">OUR PRODUCTS</a>
    <a href="#" style="width:119px">CONTACT US</a>
  </nav>
</header>

<section class="abs hero">
  <div class="abs hero-photo" role="img" aria-label="Three diamond solitaire engagement rings in white gold"></div>
  <h1 class="abs hero-title" style="font-weight:300">Welcome to<br>Our Site</h1>
  <p class="abs hero-sub">Lorem Ipsum is simply dummy text<br>of the printing and typesetting</p>
  <a class="abs hero-btn">Read More</a>
  <div class="abs dots"><span></span><span></span><span class="on"></span><span></span><span></span></div>
  <div class="abs arrow" style="left:0"><svg width="20" height="34" viewBox="0 0 20 34"><polyline points="17,2 3,17 17,32" fill="none" stroke="#fff" stroke-width="2"/></svg></div>
  <div class="abs arrow" style="left:1030px"><svg width="20" height="34" viewBox="0 0 20 34"><polyline points="3,2 17,17 3,32" fill="none" stroke="#fff" stroke-width="2"/></svg></div>
</section>

<section>
  <div class="abs cat" style="left:128px">
    <div class="cat-photo" role="img" aria-label="Curved diamond necklace pendant"></div>
    <h3>Necklaces</h3>
    <p>Lorem Ipsum is simply dummy text of the<br>printing and typesetting</p>
    <span class="more">more <svg width="8" height="14" viewBox="0 0 8 14"><polyline points="1,1 7,7 1,13" fill="none" stroke="#ddd" stroke-width="1.4"/></svg></span>
  </div>
  <div class="abs vrule" style="left:414px"></div>
  <div class="abs cat" style="left:411px">
    <div class="cat-photo" role="img" aria-label="Diamond halo drop earring"></div>
    <h3>Earrings</h3>
    <p>Lorem Ipsum is simply dummy text of the<br>printing and typesetting</p>
    <span class="more">more <svg width="8" height="14" viewBox="0 0 8 14"><polyline points="1,1 7,7 1,13" fill="none" stroke="#ddd" stroke-width="1.4"/></svg></span>
  </div>
  <div class="abs vrule" style="left:693px"></div>
  <div class="abs cat" style="left:690px">
    <div class="cat-photo" role="img" aria-label="Diamond channel-set bracelet link"></div>
    <h3>Bracelets</h3>
    <p>Lorem Ipsum is simply dummy text of the<br>printing and typesetting</p>
    <span class="more">more <svg width="8" height="14" viewBox="0 0 8 14"><polyline points="1,1 7,7 1,13" fill="none" stroke="#ddd" stroke-width="1.4"/></svg></span>
  </div>
</section>

<section class="abs panel" style="left:141px">
  <svg class="abs" style="left:21px;top:23px" width="74" height="72" viewBox="0 0 74 72" fill="none" stroke="#4a4a8a" stroke-width="3" stroke-linejoin="round">
    <polygon points="14,4 60,4 72,24 37,69 2,24"/>
    <line x1="2" y1="24" x2="72" y2="24"/>
    <polyline points="14,4 24,24 37,69 50,24 60,4"/>
    <polyline points="24,24 37,4 50,24"/>
  </svg>
  <h2 style="left:115px;top:16px">Custom Jewellery</h2>
  <p class="abs custom-sub">Create your own jewellery</p>
  <p class="abs custom-body">Lorem Ipsum is simply dummy text of the printing and typesetting industry. Lorem Ipsum has been the industry's standard</p>
  <span class="abs more-light">more <svg width="8" height="14" viewBox="0 0 8 14"><polyline points="1,1 7,7 1,13" fill="none" stroke="#333" stroke-width="1.4"/></svg></span>
</section>

<section class="abs panel" style="left:564px">
  <h2 style="left:19px;top:14px">Engagement Ring</h2>
  <div class="abs field" style="left:21px;top:49px">Name</div>
  <div class="abs field" style="left:200px;top:49px">EMail</div>
  <div class="abs field" style="left:21px;top:84px">Phone</div>
  <div class="abs field" style="left:200px;top:84px">Competitor Link</div>
  <div class="abs field" style="left:21px;top:122px">Budget</div>
  <div class="abs submit" style="left:200px;top:122px">Submit</div>
</section>

<footer class="abs footer">
  <p class="abs footer-lines">Exquisite craftsmanship Finest quality diamonds<br>Will beat any competitors price by twenty to seventy percent guaranteed<br>Price quotes within 24 hours</p>
  <div class="abs connect">Connect with us
    <div class="social"><span aria-label="Social link"></span><span aria-label="Social link" style="background:#b8403a"></span><span aria-label="Social link" style="background:#4b8fc9"></span><span aria-label="Social link" style="background:#b8403a"></span></div>
  </div>
  <div class="abs footer-rule"></div>
  <p class="abs copy">Copyrights @ 2013 All Rights Reserved</p>
</footer>

</body>
</html>
```